Brook Refrigeration. Refrigeration and air conditioning specialists.

We need a website to promote our business. We would a modern simple design using the colours from our logo and black. We want it to be fun but proffesional.

Target Market(s)

Commercial

Number of Pages Required

4 page

Requirements
Must have
• Home Page, About Us, Services and Contact Us.
• 24/7 365 days service available.
• Brook Refrigeration's dedicated team specialises in commercial refrigeration and air conditioning equipment.
• Based in Joondalup, we cover Perth Metro and surrounding areas.
Nice to have
• KNOWLEDGE . EXPERIENCE . PASSION in bold.
• Our experienced and highly trained technicians provide extensive knowledge and exceptional skills for your commercial refrigeration and air conditioning requirements.
• Pictures of commercial refrigeration.
Should not have
• No mention of domestic services.

```html
<!DOCTYPE html>
<html lang="en">
<head>
<meta charset="utf-8">
<title>Contact Us – Brook Refrigeration</title>
<link rel="stylesheet" href="https://fonts.googleapis.com/css2?family=Lato:wght@400;700;900&display=swap">
<style>
:root{
  --lime:#9cf25a;
  --lime-deep:#7fd94a;
  --plum:#2d1b4e;
  --ink:#222;
  --grey:#555;
  --rule:#e4e4e4;
  --white:#fff;
}
*{margin:0;padding:0;box-sizing:border-box}
html,body{width:699px;height:1200px;overflow:hidden;background:var(--white)}
body{position:relative;font-family:'Lato',sans-serif;color:var(--ink)}
.abs{position:absolute}
.brand{font-weight:900;color:var(--lime-deep);font-size:21px;line-height:1.05;letter-spacing:.5px}
.follow-label{left:436px;top:13px;font-size:9px;font-weight:700;color:var(--plum)}
.social-dot{width:11px;height:11px;border-radius:50%;background:var(--plum)}
.top-phone{left:556px;top:9px;font-size:14px;font-weight:900;color:var(--plum);display:flex;align-items:center;gap:6px}
.nav{top:39px;right:43px;display:flex;gap:6px;font-size:9px;font-weight:700}
.nav a{display:block;padding:7px 9px;color:var(--ink);text-decoration:none}
.nav a.active{background:var(--lime)}
.hero{left:0;top:68px;width:699px;height:114px;background:linear-gradient(100deg,#6fd83c 0%,#82cc58 25%,#4a6a4a 55%,#3b2d55 80%,#3a2258 100%)}
.hero h1{position:absolute;width:100%;top:47px;text-align:center;color:var(--white);font-size:17px;font-weight:900}
.info-title{left:45px;top:236px;font-size:11px;font-weight:900;color:var(--plum)}
.info-line{left:45px;font-size:11px;color:var(--ink);display:flex;align-items:center;gap:10px}
.btn{background:var(--lime);color:var(--plum);font-size:9px;font-weight:900;display:flex;align-items:center;justify-content:center}
.photo{left:410px;top:216px;width:247px;height:167px;background:linear-gradient(135deg,#a58a7a,#c8c4bf 50%,#8e9296)}
.rule{left:44px;top:415px;width:612px;height:1px;background:var(--rule)}
.section-title{width:100%;text-align:center;font-size:17px;font-weight:900}
.map{left:44px;top:486px;width:612px;height:184px;background:linear-gradient(120deg,#e6ebe4,#dfe7dc 50%,#e8e6df)}
.quick{left:0;top:688px}
.field{background:var(--white);font-size:9px;color:#555;padding:11px 9px}
.foot-head{font-size:9px;font-weight:900;color:var(--plum)}
.foot-text{font-size:8px;color:var(--ink);line-height:1}
.foot-small{font-size:7px;color:var(--grey)}
</style>
</head>
<body>
<header>
  <div class="abs brand" style="left:44px;top:14px">Brook<br>Refrigeration</div>
  <div class="abs follow-label">FOLLOW US</div>
  <span class="abs social-dot" style="left:492px;top:12px" aria-label="Social link"></span>
  <span class="abs social-dot" style="left:512px;top:12px" aria-label="Social link"></span>
  <div class="abs top-phone">
    <svg width="10" height="10" viewBox="0 0 24 24"><path fill="#2d1b4e" d="M6.6 10.8a15 15 0 006.6 6.6l2.2-2.2a1 1 0 011-.25 11.4 11.4 0 003.6.57 1 1 0 011 1V20a1 1 0 01-1 1A17 17 0 013 4a1 1 0 011-1h3.5a1 1 0 011 1c0 1.25.2 2.45.57 3.57a1 1 0 01-.25 1z"/></svg>
    1300-555-018
  </div>
  <nav class="abs nav">
    <a href="#">HOME</a><a href="#">ABOUT</a><a href="#">SERVICES</a><a href="#" class="active">CONTACT</a>
  </nav>
</header>

<section class="abs hero"><h1>CONTACT US</h1></section>

<section>
  <div class="abs info-title">BROOK REFRIGERATION</div>
  <div class="abs info-line" style="top:257px">12 Lakeside Drive Joondalup, WA 6027</div>
  <div class="abs info-line" style="top:277px">
    <svg width="9" height="9" viewBox="0 0 24 24"><path fill="#222" d="M6.6 10.8a15 15 0 006.6 6.6l2.2-2.2a1 1 0 011-.25 11.4 11.4 0 003.6.57 1 1 0 011 1V20a1 1 0 01-1 1A17 17 0 013 4a1 1 0 011-1h3.5a1 1 0 011 1c0 1.25.2 2.45.57 3.57a1 1 0 01-.25 1z"/></svg>
    1-800-555-0142</div>
  <div class="abs info-line" style="top:297px">
    <svg width="10" height="8" viewBox="0 0 20 16"><rect width="20" height="16" fill="#222"/><path d="M0 1l10 7 10-7" stroke="#fff" stroke-width="1.5" fill="none"/></svg>
    hello@brookrefrigeration.com</div>
  <div class="abs btn" style="left:44px;top:335px;width:88px;height:26px">CONTACT US</div>
  <div class="abs photo" role="img" aria-label="Technician servicing a rooftop commercial air conditioning unit"></div>
</section>

<div class="abs rule"></div>

<section>
  <h2 class="abs section-title" style="top:444px;color:var(--plum)">LOCATION MAP</h2>
  <div class="abs map" role="img" aria-label="Street map showing the business location"></div>
</section>

<section class="abs quick" style="width:699px;height:376px">
  <svg class="abs" style="left:0;top:0" width="699" height="376" role="img" aria-label="Commercial supermarket refrigeration aisle">
    <defs><linearGradient id="aisle" x1="0" y1="0" x2="1" y2="1"><stop offset="0" stop-color="#4b4f55"/><stop offset=".5" stop-color="#5d6166"/><stop offset="1" stop-color="#3c3f44"/></linearGradient></defs>
    <polygon points="0,36 699,0 699,336 0,376" fill="url(#aisle)"/>
  </svg>
  <h2 class="abs section-title" style="top:65px;color:var(--white)">QUICK CONTACT</h2>
  <div class="abs field" style="left:132px;top:108px;width:210px;height:29px">Name</div>
  <div class="abs field" style="left:358px;top:108px;width:210px;height:29px">Phone Name</div>
  <div class="abs field" style="left:132px;top:147px;width:210px;height:29px">Email Address</div>
  <div class="abs field" style="left:358px;top:147px;width:210px;height:29px">Company Name</div>
  <div class="abs field" style="left:132px;top:186px;width:436px;height:78px">Message</div>
  <div class="abs btn" style="left:306px;top:283px;width:88px;height:26px">SUBMIT</div>
</section>

<footer>
  <div class="abs brand" style="left:44px;top:1082px;font-size:19px">Brook<br>Refrigeration</div>
  <div class="abs foot-small" style="left:44px;top:1133px;line-height:14px">Copyright © 2018 Brook Refrigeration Pty Ltd.<br>All Rights Reserved.<br>ABN 51 824 307 116</div>

  <div class="abs foot-head" style="left:242px;top:1078px">SITE MAP</div>
  <div class="abs foot-text" style="left:242px;top:1097px">Home</div>
  <div class="abs foot-text" style="left:242px;top:1116px">About</div>
  <div class="abs foot-text" style="left:242px;top:1135px">Services</div>
  <div class="abs foot-text" style="left:242px;top:1154px">Contact Us</div>

  <div class="abs foot-head" style="left:366px;top:1078px">CONTACT US</div>
  <div class="abs foot-text" style="left:366px;top:1096px;line-height:12px">12 Lakeside Drive<br>Joondalup, WA 6027</div>
  <div class="abs foot-text" style="left:366px;top:1124px;display:flex;gap:12px;align-items:center">
    <svg width="7" height="7" viewBox="0 0 24 24"><path fill="#222" d="M6.6 10.8a15 15 0 006.6 6.6l2.2-2.2a1 1 0 011-.25 11.4 11.4 0 003.6.57 1 1 0 011 1V20a1 1 0 01-1 1A17 17 0 013 4a1 1 0 011-1h3.5a1 1 0 011 1c0 1.25.2 2.45.57 3.57a1 1 0 01-.25 1z"/></svg>1-800-555-0142</div>
  <div class="abs foot-text" style="left:366px;top:1140px;display:flex;gap:12px;align-items:center">
    <svg width="7" height="6" viewBox="0 0 20 16"><rect width="20" height="16" fill="#222"/><path d="M0 1l10 7 10-7" stroke="#fff" stroke-width="1.5" fill="none"/></svg>hello@brookrefrigeration.com</div>
  <div class="abs foot-text" style="left:366px;top:1156px;display:flex;gap:12px;align-items:center">
    <svg width="7" height="8" viewBox="0 0 12 16"><path fill="#222" d="M6 0a6 6 0 00-6 6c0 4.5 6 10 6 10s6-5.5 6-10a6 6 0 00-6-6zm0 8.5A2.5 2.5 0 116 3.5a2.5 2.5 0 010 5z"/></svg>Map Direction</div>

  <div class="abs foot-head" style="left:529px;top:1078px">FOLLOW US</div>
  <span class="abs social-dot" style="left:529px;top:1101px;background:var(--ink)" aria-label="Social link"></span>
  <span class="abs social-dot" style="left:548px;top:1101px;background:var(--ink)" aria-label="Social link"></span>
</footer>
</body>
</html>
```